Business Card Design

We provide services doing multiple jobs in the construction industry.Please note: The company name needs to be ROCK SOLID BUILDING SERVICESAttached logo was an example of what we wanted. Can you change up the colors?

Industry/Entity Type

Construction

Contact Information for Business Card

ROCK SOLID BUILDING SERVICES5401 HUDSON BEND RDAUSTIN, TX 78734(512)243-6854ROCKSOLIDBUILDINGSERVICES@GMAIL.COM

```html
<!DOCTYPE html>
<html lang="en">
<head>
<meta charset="utf-8">
<title>Pearlwood Framing Works – Business Card</title>
<link rel="stylesheet" href="https://fonts.googleapis.com/css2?family=Archivo+Black&family=Arimo:wght@400;700&display=swap">
<style>
  :root {
    --page-bg: #e9e9e7;
    --card-white: #ffffff;
    --card-shade: #f1f1f1;
    --band-black: #050505;
    --band-text: #ffffff;
    --muted-text: #9a9a9a;
    --ink: #111111;
    --brand-blue: #2c3f86;
  }
  * { margin: 0; padding: 0; box-sizing: border-box; }
  html, body {
    width: 1200px;
    height: 848px;
    overflow: hidden;
    background: var(--page-bg);
  }
  .canvas {
    position: relative;
    width: 1200px;
    height: 848px;
  }
  .card {
    position: absolute;
    left: 180px;
    top: 184px;
    width: 840px;
    height: 480px;
    border-radius: 36px;
    overflow: hidden;
    background: linear-gradient(180deg, var(--card-white) 0%, var(--card-shade) 100%);
    box-shadow: 0 10px 30px rgba(0,0,0,0.18);
  }
  .card__band {
    position: absolute;
    inset: 0;
    width: 840px;
    height: 480px;
  }
  .brand-mark {
    position: absolute;
    top: 52px;
    left: 0;
    width: 100%;
    display: flex;
    justify-content: center;
    align-items: center;
    gap: 10px;
    font-family: "Arimo", Arial, sans-serif;
    font-weight: 700;
    font-size: 22px;
    letter-spacing: 1px;
    color: var(--brand-blue);
  }
  .brand-mark__square {
    width: 18px;
    height: 18px;
    background: var(--brand-blue);
  }
  .company {
    position: absolute;
    top: 172px;
    left: 0;
    width: 100%;
    text-align: center;
    color: var(--band-text);
  }
  .company__name {
    font-family: "Archivo Black", "Arial Black", sans-serif;
    font-size: 62px;
    line-height: 1;
    letter-spacing: 1px;
  }
  .company__tagline {
    margin-top: 6px;
    font-family: "Arimo", Arial, sans-serif;
    font-size: 17px;
    letter-spacing: 1px;
    color: var(--muted-text);
  }
  .contact {
    position: absolute;
    top: 352px;
    left: 0;
    width: 100%;
    text-align: center;
    font-family: "Arimo", Arial, sans-serif;
    font-size: 21px;
    line-height: 30px;
    color: var(--ink);
  }
</style>
</head>
<body>
<main class="canvas">
  <article class="card">
    <svg class="card__band" viewBox="0 0 840 480" aria-hidden="true">
      <path d="M0,30 Q420,210 840,30 L840,450 Q420,230 0,450 Z" fill="var(--band-black)"/>
    </svg>

    <div class="brand-mark">
      <span class="brand-mark__square"></span>
      <span class="brand-mark__name">PEARLWOOD PLUMBING CO</span>
    </div>

    <header class="company">
      <h1 class="company__name">PEARLWOOD</h1>
      <p class="company__tagline">FRAMING WORKS</p>
    </header>

    <address class="contact">
      <p class="contact__phone">(512)555-0193</p>
      <p class="contact__address">7732 FERNGLEN PASS LN AUSTIN, TX 78734</p>
      <p class="contact__email">PEARLWOODFRAMINGWORKS@MAILNEST.EXAMPLE</p>
    </address>
  </article>
</main>
</body>
</html>
```